Modern design company business card design

We are a design oriented construction firm. The owner is an architect and licensed General Contractor and accomplished furniture designer. We do new home construction and large scale remodeling and office design. We would like a design for our new business cards that is clean and modern, but relatable. We like the bright green color of our logo mixed with different shades of grey. We're also open to reinterpreting the logo.

Target Market(s)

Potential design clients,
Construction clients

Industry/Entity Type

Architecture

Contact Information for Business Card

Tall Maple Design | Build Inc. (optional with logo, Inc. optional)Jeffrey MorganOwner (optional)317.555.0148 cell317.431.8056 officejmorgan@greensquareinc.comwww.greensquareinc.com

Font styles to use
Sans Serif
Other font styles liked:
• Avenir

Requirements
Nice to have
• I like designs that have some continuity between the front and back, i.e. similar layouts or graphic elements that wrap around the card. I tend to prefer horizontal over vertical, but that's not a have to. I also tend to prefer white or recycled paper.

```html
<!DOCTYPE html>
<html lang="en">
<head>
<meta charset="utf-8">
<title>Tall Maple Design | Build — Business Cards</title>
<link href="https://fonts.googleapis.com/css2?family=Mulish:wght@400;600;700&display=swap" rel="stylesheet">
<style>
  :root {
    --bg: #ecebe8;
    --card: #ffffff;
    --green-light: #b5dd6a;
    --green: #5cb547;
    --green-deep: #2f9a3f;
    --grey-dark: #4d4d4d;
    --grey: #7a7a7a;
    --white: #ffffff;
  }
  * { box-sizing: border-box; margin: 0; padding: 0; }
  html, body { width: 1200px; height: 913px; overflow: hidden; }
  body {
    background: var(--bg);
    font-family: "Mulish", "Helvetica Neue", Arial, sans-serif;
    position: relative;
  }
  .card {
    position: absolute;
    width: 630px;
    height: 360px;
    background: var(--card);
    border-radius: 18px;
    overflow: hidden;
    box-shadow: 0 6px 22px rgba(0,0,0,0.12);
  }
  .card--front { left: 90px; top: 70px; }
  .card--back { left: 480px; top: 483px; }

  /* Front */
  .front__band {
    position: absolute;
    left: 0; right: 0; bottom: 0;
    height: 150px;
    background: linear-gradient(100deg, var(--green-light) 0%, var(--green) 45%, var(--green-deep) 100%);
  }
  .front__rule {
    position: absolute;
    height: 2px;
    background: var(--green);
  }
  .front__rule--upper { left: 170px; right: 30px; top: 84px; }
  .front__rule--lower { left: 34px; right: 0; top: 190px; }
  .front__tab {
    position: absolute;
    right: 0; top: 34px;
    width: 44px; height: 26px;
    background: linear-gradient(90deg, var(--green-light), var(--green));
  }
  .person__name {
    position: absolute;
    right: 56px; top: 44px;
    font-weight: 700;
    font-size: 22px;
    line-height: 28px;
    letter-spacing: 0.5px;
    color: var(--grey-dark);
    text-transform: uppercase;
  }
  .person__role {
    position: absolute;
    right: 56px; top: 92px;
    font-size: 13px;
    line-height: 16px;
    color: var(--green);
  }

  .brand {
    position: absolute;
    display: flex;
    align-items: center;
    gap: 10px;
  }
  .brand__dot {
    border-radius: 50%;
    background: var(--green);
    flex: none;
  }
  .brand__name {
    color: var(--grey);
    font-weight: 600;
    white-space: nowrap;
  }
  .card--front .brand { left: 34px; top: 130px; }
  .card--front .brand__dot { width: 14px; height: 14px; }
  .card--front .brand__name { font-size: 20px; line-height: 26px; }

  .contacts {
    position: absolute;
    left: 60px; top: 226px;
    list-style: none;
    color: var(--white);
    font-size: 15px;
    line-height: 26px;
  }
  .contacts li { display: flex; align-items: center; gap: 9px; }
  .contacts svg { width: 13px; height: 13px; flex: none; }

  /* Back */
  .card--back .brand { left: 0; right: 0; top: 160px; justify-content: center; gap: 14px; }
  .card--back .brand__dot { width: 22px; height: 22px; }
  .card--back .brand__name { font-size: 30px; line-height: 40px; }
</style>
</head>
<body>

<section class="card card--front" aria-label="Business card front">
  <div class="front__tab"></div>
  <div class="person__name">Dennis Holloway</div>
  <div class="front__rule front__rule--upper"></div>
  <div class="person__role">Owner</div>

  <div class="brand">
    <div class="brand__dot"></div>
    <div class="brand__name">Tall Maple Design | Build</div>
  </div>

  <div class="front__rule front__rule--lower"></div>
  <div class="front__band"></div>

  <ul class="contacts">
    <li>
      <svg viewBox="0 0 16 16" aria-hidden="true"><rect x="4" y="1" width="8" height="14" rx="1.5" fill="none" stroke="#fff" stroke-width="1.6"/><circle cx="8" cy="12.5" r="0.9" fill="#fff"/></svg>
      317.555.0148
    </li>
    <li>
      <svg viewBox="0 0 16 16" aria-hidden="true"><path d="M4 1.5l2.5 3-1.6 1.6c.8 1.8 2.2 3.2 4 4l1.6-1.6 3 2.5-1.7 2.5C6.5 13.8 2.2 9.5 1.5 4.2z" fill="#fff"/></svg>
      317.555.0172
    </li>
    <li>
      <svg viewBox="0 0 16 16" aria-hidden="true"><circle cx="8" cy="8" r="6.5" fill="none" stroke="#fff" stroke-width="1.4"/><ellipse cx="8" cy="8" rx="2.8" ry="6.5" fill="none" stroke="#fff" stroke-width="1.2"/><line x1="1.5" y1="8" x2="14.5" y2="8" stroke="#fff" stroke-width="1.2"/></svg>
      www.tallmapleinc.example
    </li>
    <li>
      <svg viewBox="0 0 16 16" aria-hidden="true"><rect x="1.5" y="3.5" width="13" height="9" fill="none" stroke="#fff" stroke-width="1.4"/><path d="M1.5 3.5L8 9l6.5-5.5" fill="none" stroke="#fff" stroke-width="1.4"/></svg>
      dholloway@tallmapleinc.example
    </li>
  </ul>
</section>

<section class="card card--back" aria-label="Business card back">
  <div class="brand">
    <div class="brand__dot"></div>
    <div class="brand__name">Tall Maple Design | Build</div>
  </div>
</section>

</body>
</html>
```